Mosquito and outdoor pest management

The uploaded logo must be integrated as the main theme of the card. I would like it to be modern and eye catching. Maybe some backround images or light silver metallic background.
Space enough at the base for contact info to be put in- phone numbers,emails,names,website.
Space on the back for short blog and lines for hand writing..calling card.
Commercial- golf courses, schools, outdoor function properties, pre event treatments.
Residential- retirement villages, townhome complexes and general houses
Management

```html
<!DOCTYPE html>
<html lang="en">
<head>
<meta charset="utf-8">
<title>Bayline Mosquito – Business Card</title>
<link href="https://fonts.googleapis.com/css2?family=Open+Sans:wght@400;600&display=swap" rel="stylesheet">
<style>
  :root {
    --stage: #3b3b3b;
    --card-light: #ffffff;
    --card-mid: #e4e4e4;
    --card-edge: #c9c9c9;
    --ink: #1a1a1a;
    --ink-soft: #555555;
    --accent: #e8202a;
    --rule: #8a8a8a;
  }
  * { box-sizing: border-box; margin: 0; padding: 0; }
  html, body {
    width: 1105px; height: 1200px; overflow: hidden;
    background: var(--stage);
    font-family: "Open Sans", Arial, sans-serif;
  }
  .card {
    position: absolute; left: 192px; width: 720px; height: 412px;
    background: radial-gradient(ellipse at 55% 45%, var(--card-light) 0%, var(--card-mid) 65%, var(--card-edge) 100%);
  }
  .card--front { top: 146px; }
  .card--back { top: 598px; }

  .brand { position: absolute; left: 122px; top: 92px; color: var(--ink); font-weight: 600; }
  .brand__name { display: flex; align-items: center; gap: 14px; font-size: 46px; line-height: 1; letter-spacing: 0.5px; }
  .brand__dot { width: 22px; height: 22px; border-radius: 50%; background: var(--accent); }
  .brand__tagline { margin-top: 6px; font-size: 17px; letter-spacing: 1.5px; text-transform: uppercase; }

  .person { position: absolute; right: 440px; top: 246px; text-align: right; }
  .person__name { color: var(--accent); font-size: 25px; font-weight: 600; line-height: 1.2; }
  .person__role { color: var(--ink); font-size: 19px; line-height: 1.4; }

  .divider { position: absolute; left: 308px; top: 224px; width: 1px; height: 104px; background: var(--rule); opacity: .5; }

  .contacts { position: absolute; left: 338px; top: 232px; list-style: none; }
  .contacts li { display: flex; align-items: center; gap: 10px; height: 28px; color: var(--ink-soft); font-size: 19px; }
  .contacts svg { width: 17px; height: 17px; fill: var(--accent); flex: none; }

  .base-band { position: absolute; left: 0; right: 0; bottom: 0; height: 34px; }
  .base-band__line { height: 3px; background: var(--ink); }
  .base-band__fill { height: 27px; margin-top: 4px; background: var(--accent); }

  .write-line { position: absolute; left: 28px; border-top: 2px dotted var(--rule); }
</style>
</head>
<body>
  <section class="card card--front">
    <div class="brand">
      <div class="brand__name"><span>Bayline Mosquito</span><span class="brand__dot"></span></div>
      <div class="brand__tagline">and outdoor pest management</div>
    </div>

    <div class="person">
      <div class="person__name">Aaron Hale</div>
      <div class="person__role">CEO/Founder</div>
    </div>

    <div class="divider"></div>

    <ul class="contacts">
      <li><svg viewBox="0 0 24 24"><path d="M6.6 10.8a15.1 15.1 0 0 0 6.6 6.6l2.2-2.2a1 1 0 0 1 1-.25 11.4 11.4 0 0 0 3.6.57 1 1 0 0 1 1 1V20a1 1 0 0 1-1 1A17 17 0 0 1 3 4a1 1 0 0 1 1-1h3.5a1 1 0 0 1 1 1c0 1.25.2 2.45.57 3.57a1 1 0 0 1-.25 1z"/></svg>555 210 4387</li>
      <li><svg viewBox="0 0 24 24"><path d="M2 5h20v14H2z M2 5l10 8 10-8" fill="none" stroke="#e8202a" stroke-width="0"/><path d="M2 5h20l-10 8z"/><path d="M2 7.5l10 8 10-8V19H2z"/></svg>hello@baylinepest.com</li>
      <li><svg viewBox="0 0 24 24"><circle cx="12" cy="12" r="10"/><path d="M2 12h20M12 2c3 3 3 17 0 20M12 2c-3 3-3 17 0 20" fill="none" stroke="#fff" stroke-width="1.6"/></svg>www.baylinepest.com</li>
    </ul>

    <div class="base-band">
      <div class="base-band__line"></div>
      <div class="base-band__fill"></div>
    </div>
  </section>

  <section class="card card--back">
    <div class="write-line" style="top:52px;width:659px"></div>
    <div class="write-line" style="top:97px;width:659px"></div>
    <div class="write-line" style="top:141px;width:659px"></div>
    <div class="write-line" style="top:185px;width:659px"></div>
    <div class="write-line" style="top:232px;width:659px"></div>
    <div class="write-line" style="top:279px;width:448px"></div>
    <div class="write-line" style="top:328px;width:659px"></div>
    <div class="write-line" style="top:373px;width:491px"></div>
  </section>
</body>
</html>
```